Satchel & Sundial needs new business card design

I need a new business card design. I'm looking for out-of-the-box design which represents the freedom of being a location independent entrepreneur.
I offer coaching, retreats and trips.
I would like to see designs with and without the photo.
Colors I use are black (#000000), green (#25A796) and brown (#D7C38C)
Website satchelandsundial.example

Target Market(s)

location independent entrepreneurs, digital nomads, people looking to swap the 9 to 5 for a lifestyle business

Industry/Entity Type

Business

Contact Information for Business Card

Dorota Falkner
Your Lifestyle Business Coach, Retreat & Trip Leader
http://satchelandsundial.example
hello@satchelandsundial.example
Live a life you don't need a holiday from

Font styles to use
Serif
Sans Serif

Requirements
Must have
• One side should contain only the logo. I would also consider having the "Live a life you don't need a holiday from" on that side too (depending on how it looks)
• Please show both sides on the designs.

```html
<!DOCTYPE html>
<html lang="en">
<head>
<meta charset="utf-8">
<title>Satchel &amp; Sundial — Business Card</title>
<link rel="stylesheet" href="https://fonts.googleapis.com/css2?family=Source+Sans+3:wght@400;600&display=swap">
<style>
  :root {
    --stage: #d6d6d6;
    --card-front: #ffffff;
    --card-back: #231f20;
    --ink: #231f20;
    --ink-soft: #555555;
    --teal: #25a796;
    --rule: #bdbdbd;
    --white: #ffffff;
  }
  * { box-sizing: border-box; margin: 0; padding: 0; }
  html, body {
    width: 1105px;
    height: 1200px;
    overflow: hidden;
  }
  body {
    background: var(--stage);
    font-family: "Source Sans 3", "Myriad Pro", Arial, sans-serif;
    position: relative;
  }
  .card {
    position: absolute;
    left: 196px;
    width: 720px;
    height: 413px;
  }
  .card--front { top: 145px; background: var(--card-front); }
  .card--back  { top: 602px; background: var(--card-back); }

  /* Front */
  .brand-name {
    position: absolute;
    font-weight: 600;
    white-space: nowrap;
  }
  .card--front .brand-name {
    left: 46px;
    top: 172px;
    font-size: 34px;
    color: var(--ink);
  }
  .divider {
    position: absolute;
    left: 356px;
    top: 124px;
    width: 1px;
    height: 159px;
    background: var(--rule);
  }
  .contact {
    position: absolute;
    left: 381px;
    top: 128px;
  }
  .contact__name {
    font-size: 26px;
    font-weight: 600;
    color: var(--teal);
    line-height: 32px;
  }
  .contact__role {
    font-size: 19.5px;
    color: var(--ink);
    line-height: 28px;
    margin-top: 1px;
  }
  .contact__list {
    list-style: none;
    margin-top: 16px;
  }
  .contact__item {
    display: flex;
    align-items: center;
    gap: 9px;
    font-size: 18.5px;
    color: var(--ink-soft);
    line-height: 28px;
  }
  .contact__icon { width: 17px; height: 17px; flex: none; }

  /* Back */
  .social {
    position: absolute;
    top: 25px;
    right: 23px;
    display: flex;
    gap: 5px;
  }
  .social__tile {
    width: 26px;
    height: 26px;
    background: var(--teal);
  }
  .card--back .brand-name {
    left: 0;
    right: 0;
    top: 188px;
    text-align: center;
    font-size: 48px;
    color: var(--white);
  }
  .tagline {
    position: absolute;
    left: 0;
    right: 0;
    top: 341px;
    text-align: center;
    font-size: 18.5px;
    letter-spacing: 0.2px;
    text-transform: uppercase;
    color: var(--white);
  }
</style>
</head>
<body>
  <section class="card card--front" aria-label="Business card front">
    <div class="brand-name">Satchel &amp; Sundial</div>
    <div class="divider"></div>
    <div class="contact">
      <p class="contact__name">Dorota Falkner</p>
      <p class="contact__role">Your Lifestyle Business Coach<br>Retreat &amp; Trip Leader</p>
      <ul class="contact__list">
        <li class="contact__item">
          <svg class="contact__icon" viewBox="0 0 16 16" aria-hidden="true">
            <rect x="1" y="3" width="14" height="10" fill="var(--teal)"/>
            <path d="M1.5 3.5 L8 9 L14.5 3.5" fill="none" stroke="#fff" stroke-width="1.3"/>
          </svg>
          hello@satchelandsundial.example
        </li>
        <li class="contact__item">
          <svg class="contact__icon" viewBox="0 0 16 16" aria-hidden="true">
            <circle cx="8" cy="8" r="7" fill="var(--teal)"/>
            <ellipse cx="8" cy="8" rx="3" ry="7" fill="none" stroke="#fff" stroke-width="1"/>
            <line x1="1" y1="8" x2="15" y2="8" stroke="#fff" stroke-width="1"/>
          </svg>
          www.satchelandsundial.example
        </li>
      </ul>
    </div>
  </section>

  <section class="card card--back" aria-label="Business card back">
    <div class="social" aria-label="Social profiles">
      <span class="social__tile"></span>
      <span class="social__tile"></span>
      <span class="social__tile"></span>
    </div>
    <div class="brand-name">Satchel &amp; Sundial</div>
    <p class="tagline">Live a life you don’t need a holiday from</p>
  </section>
</body>
</html>
```